Business Card

Just need business logo with phone number on it. 0487 312 654
And the following on the bottom of the card.

"Your local plumbing experts".
and emblems for zelpa card, cheque and cash

```html
<!DOCTYPE html>
<html lang="en">
<head>
<meta charset="utf-8">
<title>Ridgeline Plumbing &amp; Drainage – Business Card</title>
<link rel="stylesheet" href="https://fonts.googleapis.com/css2?family=Roboto:wght@500;700;900&display=swap">
<style>
  :root {
    --stage: #2b2b2d;
    --card-white: #ffffff;
    --brand-red: #e8232d;
    --brand-blue: #1b8fd1;
    --ink-white: #ffffff;
    --cash-green: #3b6b4a;
    --cheque-blue: #2f4f6e;
    --zelpa-navy: #1f2f6b;
  }
  * { box-sizing: border-box; margin: 0; padding: 0; }
  html, body { width: 1200px; height: 880px; overflow: hidden; }
  body {
    background: var(--stage);
    font-family: "Roboto", Arial, sans-serif;
    display: flex;
    flex-direction: column;
    align-items: center;
    justify-content: center;
    gap: 40px;
  }
  .card {
    width: 700px;
    height: 400px;
    border-radius: 26px;
    position: relative;
    overflow: hidden;
  }

  /* Front */
  .card--front {
    background: var(--card-white);
    display: flex;
    align-items: center;
    justify-content: center;
  }
  .wordmark {
    color: var(--brand-red);
    font-weight: 900;
    text-transform: uppercase;
    text-align: center;
    line-height: 1.05;
  }
  .wordmark__name { display: block; font-size: 52px; letter-spacing: 2px; }
  .wordmark__trade { display: block; font-size: 19px; letter-spacing: 5px; margin-top: 6px; }
  .wordmark__suffix { display: block; font-size: 11px; letter-spacing: 3px; margin-top: 6px; }

  /* Back */
  .card--back { background: var(--brand-red); }
  .back__feature {
    position: absolute; inset: 0;
    width: 100%; height: 100%;
  }
  .back__content {
    position: absolute;
    left: 48px; top: 70px;
    width: 370px;
    display: flex;
    flex-direction: column;
    align-items: flex-start;
    color: var(--ink-white);
  }
  .back__content .wordmark { color: var(--ink-white); text-align: left; }
  .back__content .wordmark__name { font-size: 44px; }
  .back__content .wordmark__trade { font-size: 16px; letter-spacing: 4px; }
  .phone {
    margin-top: 34px;
    font-size: 32px;
    font-weight: 700;
    letter-spacing: 1px;
  }
  .payments {
    margin-top: 30px;
    display: flex;
    align-items: center;
    gap: 18px;
  }
  .payment-zelpa {
    display: flex; align-items: center; gap: 8px;
    background: var(--ink-white);
    border-radius: 5px;
    padding: 7px 12px;
    color: var(--zelpa-navy);
    font-weight: 700;
    font-size: 18px;
  }
  .payment-zelpa__dot { width: 10px; height: 10px; background: var(--zelpa-navy); }
  .payment-cash {
    width: 46px; height: 46px; border-radius: 50%;
    background: var(--cash-green);
    border: 3px solid var(--ink-white);
  }
  .payment-cheque {
    width: 62px; height: 40px; border-radius: 6px;
    background: var(--cheque-blue);
    border: 3px solid var(--ink-white);
  }
  .tagline {
    margin-top: 26px;
    font-size: 19px;
    font-weight: 500;
    letter-spacing: 1.5px;
  }
</style>
</head>
<body>

  <section class="card card--front" aria-label="Card front">
    <p class="wordmark">
      <span class="wordmark__name">Ridgeline</span>
      <span class="wordmark__trade">Plumbing &amp; Drainage</span>
      <span class="wordmark__suffix">Pty Ltd</span>
    </p>
  </section>

  <section class="card card--back" aria-label="Card back">
    <svg class="back__feature" viewBox="0 0 700 400" role="img" aria-label="Large water drop illustration in white and blue">
      <defs>
        <linearGradient id="featureFill" x1="0" y1="0.3" x2="1" y2="0.7">
          <stop offset="0" stop-color="#ffffff"/>
          <stop offset="0.55" stop-color="#dcecf7"/>
          <stop offset="1" stop-color="#1b8fd1"/>
        </linearGradient>
      </defs>
      <path d="M440 0 C470 140 520 300 470 400 H700 V0 Z" fill="url(#featureFill)"/>
    </svg>

    <div class="back__content">
      <p class="wordmark">
        <span class="wordmark__name">Ridgeline</span>
        <span class="wordmark__trade">Plumbing &amp; Drainage</span>
      </p>
      <p class="phone">0487 312 654</p>
      <div class="payments">
        <span class="payment-zelpa"><span class="payment-zelpa__dot"></span>zelpa</span>
        <span class="payment-cash" role="img" aria-label="Cash accepted"></span>
        <span class="payment-cheque" role="img" aria-label="Cheque accepted"></span>
      </div>
      <p class="tagline">Your local plumbing experts</p>
    </div>
  </section>

</body>
</html>
```